Corvane Freight Company Business Card Design

We are a company that delivers natural saltwater (from the ocean) to aquarium companies, restaurants and home marine tanks. I would like a new business card to suit.

Must include Name, company name, abn, contact number and website as well as logo (see attached).

Looking for a design that stands out, has a clean but unique appearance.

Double and single sided entries welcome

Business

• Logo

```html
<!DOCTYPE html>
<html lang="en">
<head>
<meta charset="utf-8">
<title>Corvane Freight Company – Business Card</title>
<link rel="stylesheet" href="https://fonts.googleapis.com/css2?family=Open+Sans:wght@400;600;700&display=swap">
<style>
  :root {
    --backdrop: #262626;
    --card-blue: #1d6fe3;
    --sky-blue: #3aa6f2;
    --band-blue: #2b8aec;
    --pale-blue: #bfe3ff;
    --white: #ffffff;
  }
  * { box-sizing: border-box; margin: 0; padding: 0; }
  html, body {
    width: 1200px; height: 1105px; overflow: hidden;
    background: var(--backdrop);
    font-family: "Open Sans", Arial, sans-serif;
  }
  .canvas { position: relative; width: 1200px; height: 1105px; }
  .card {
    position: absolute; width: 789px; height: 450px;
    border-radius: 30px; overflow: hidden;
    background: var(--card-blue); color: var(--white);
  }
  .card--front { left: 69px; top: 75px; }
  .card--back { left: 342px; top: 579px; }
  .card__wave { position: absolute; inset: 0; }

  .holder { position: absolute; right: 45px; top: 38px; text-align: right; }
  .holder__name { font-size: 31px; font-weight: 700; line-height: 1.2; }
  .holder__title { font-size: 22px; font-weight: 400; color: var(--pale-blue); }

  .wordmark { position: absolute; font-weight: 700; color: var(--white); white-space: nowrap; letter-spacing: -0.5px; }
  .card--front .wordmark { left: 40px; top: 170px; font-size: 50px; }
  .card--back .wordmark { left: 0; right: 0; top: 140px; text-align: center; font-size: 62px; }

  .contact { position: absolute; left: 46px; top: 326px; font-size: 17px; line-height: 30px; }
  .contact__row { display: flex; align-items: center; gap: 6px; }
  .contact__icon { width: 14px; height: 14px; }
  .divider { position: absolute; left: 264px; top: 364px; width: 1.5px; height: 56px; background: var(--pale-blue); }
  .address { position: absolute; left: 286px; top: 356px; font-size: 17px; line-height: 30px; }
  .address__company { font-weight: 700; }

  .site { position: absolute; left: 0; right: 0; top: 365px; text-align: center; font-size: 24px; letter-spacing: 4px; }
</style>
</head>
<body>
<main class="canvas">
  <section class="card card--front">
    <svg class="card__wave" viewBox="0 0 789 450" aria-hidden="true">
      <path d="M0 0H789V262C610 150 320 40 0 70Z" fill="var(--sky-blue)"/>
      <path d="M0 70C320 40 610 150 789 262V282C610 170 320 62 0 92Z" fill="var(--band-blue)"/>
      <path d="M0 72C320 42 610 152 789 264" fill="none" stroke="var(--white)" stroke-width="3"/>
    </svg>
    <div class="holder">
      <p class="holder__name">Your name</p>
      <p class="holder__title">Title</p>
    </div>
    <p class="wordmark">Corvane Freight</p>
    <div class="contact">
      <p class="contact__row">
        <svg class="contact__icon" viewBox="0 0 14 14" aria-hidden="true"><circle cx="7" cy="7" r="6" fill="none" stroke="#fff" stroke-width="1.4"/><path d="M4.5 4h2l-1 2.2 2.3 2.3 2.2-1v2c-3 .6-6-2.4-5.5-5.5z" fill="#fff"/></svg>
        123-456-7890</p>
      <p class="contact__row">
        <svg class="contact__icon" viewBox="0 0 14 14" aria-hidden="true"><circle cx="7" cy="7" r="6.5" fill="#fff"/><path d="M1 7h12M7 1c-3 3-3 9 0 12M7 1c3 3 3 9 0 12" stroke="var(--card-blue)" stroke-width="1" fill="none"/></svg>
        www.website.com</p>
      <p class="contact__row">ABN : 0123456789</p>
    </div>
    <div class="divider"></div>
    <div class="address">
      <p class="address__company">Corvane.LLC</p>
      <p>Street Name, City Name, State, City Zip Code</p>
    </div>
  </section>

  <section class="card card--back">
    <p class="wordmark">Corvane Freight</p>
    <p class="site">www.website.com</p>
  </section>
</main>
</body>
</html>
```